Modern looking signage for dental office.

Exterior signage for passing cars
Updates
Need extra days to review
Target Market(s)
Cars passing by
Font styles to use
Sans Serif
Colors
3276b5
Requirements
Must have
- Logo
- OPEN ON SUTURDAY AND SUNDAY
- NIGHT CLINIC AVAILABLE
- PLEASE USE THE FONT TYPE IN FILE 4 UPLOADED BELOW.
- (847) 302-7469
- Modern looking

```html
<!DOCTYPE html>
<html lang="en">
<head>
<meta charset="utf-8">
<title>Nova Dental – Exterior Sign</title>
<link rel="stylesheet" href="https://fonts.googleapis.com/css2?family=Open+Sans:wght@400;700;800&display=swap">
<style>
  :root {
    --page-bg: #9a9a9a;
    --sign-white: #ffffff;
    --brand-blue: #3276b5;
    --rule-black: #111111;
    --footer-grey: #dcdcdc;
    --ink-dark: #3d3d3d;
    --text-white: #ffffff;
    --divider-light: #d6e6f5;
  }
  * { margin: 0; padding: 0; box-sizing: border-box; }
  html, body { width: 1200px; height: 1000px; overflow: hidden; }
  body {
    background: var(--page-bg);
    font-family: "Open Sans", Arial, sans-serif;
    position: relative;
  }
  .sign {
    position: absolute;
    left: 193px; top: 92px;
    width: 815px; height: 816px;
    background: var(--sign-white);
    overflow: hidden;
  }
  .sign-header {
    position: absolute; left: 0; top: 0;
    width: 100%; height: 220px;
    background: var(--sign-white);
  }
  .brand-mark {
    position: absolute; left: 78px; top: 42px;
    width: 140px; height: 140px;
    border: 2px solid var(--ink-dark);
    border-radius: 50%;
  }
  .brand-name {
    position: absolute; left: 236px; top: 80px;
    width: 506px;
    text-align: center;
    font-size: 72px; font-weight: 400; letter-spacing: 1px;
    color: var(--ink-dark); line-height: 1; white-space: nowrap;
  }
  .brand-tagline {
    position: absolute; left: 282px; top: 160px;
    font-size: 27px; font-weight: 400;
    color: var(--ink-dark); line-height: 1; white-space: nowrap;
  }
  .band-rule {
    position: absolute; left: 0; width: 100%;
    background: var(--rule-black);
  }
  .band-rule--top { top: 221px; height: 9px; }
  .band-rule--bottom { top: 682px; height: 9px; }
  .hours-panel {
    position: absolute; left: 0; top: 236px;
    width: 100%; height: 440px;
    background: var(--brand-blue);
    color: var(--text-white);
    text-align: center;
  }
  .hours-panel::before, .hours-panel::after {
    content: ""; position: absolute; left: 0; width: 100%; height: 3px;
    background: var(--brand-blue);
  }
  .hours-panel::before { top: -6px; }
  .hours-panel::after { bottom: -6px; }
  .headline, .subline { position: absolute; left: 0; width: 100%; line-height: 1; font-weight: 800; white-space: nowrap; }
  .headline--open { top: 28px; font-size: 110px; }
  .subline--days { top: 141px; font-size: 53px; font-weight: 700; }
  .panel-divider {
    position: absolute; left: 172px; top: 228px;
    width: 470px; height: 2px; background: var(--divider-light);
  }
  .headline--night { top: 244px; font-size: 99px; }
  .subline--available { top: 343px; font-size: 72px; }
  .contact-bar {
    position: absolute; left: 0; top: 694px;
    width: 100%; height: 122px;
    background: var(--footer-grey);
  }
  .phone-icon { position: absolute; left: 86px; top: 23px; width: 74px; height: 74px; }
  .phone-number {
    position: absolute; left: 182px; top: 14px;
    font-size: 78px; font-weight: 700; color: var(--brand-blue);
    line-height: 1.1; white-space: nowrap; letter-spacing: 1px;
  }
</style>
</head>
<body>
  <div class="sign">
    <header class="sign-header">
      <div class="brand-mark"></div>
      <div class="brand-name">NOVA DENTAL</div>
      <div class="brand-tagline">MODERN GENERAL DENTISTRY</div>
    </header>
    <div class="band-rule band-rule--top"></div>
    <section class="hours-panel">
      <div class="headline headline--open">OPEN ON</div>
      <div class="subline subline--days">SATURDAY AND SUNDAY</div>
      <div class="panel-divider"></div>
      <div class="headline headline--night">NIGHT CLINIC</div>
      <div class="subline subline--available">AVAILABLE</div>
    </section>
    <div class="band-rule band-rule--bottom"></div>
    <footer class="contact-bar">
      <svg class="phone-icon" viewBox="0 0 74 74" aria-hidden="true">
        <circle cx="37" cy="37" r="33" fill="none" stroke="#3276b5" stroke-width="6"/>
        <path d="M26 20c2-1 4 0 5 2l3 6c1 2 0 3-1 4l-2 2c2 4 5 7 9 9l2-2c1-1 3-2 4-1l6 3c2 1 3 3 2 5l-2 4c-1 2-4 3-7 2-11-3-20-12-23-23-1-3 0-6 2-7z" fill="#3276b5"/>
        <path d="M42 22a11 11 0 0 1 10 10M42 15a18 18 0 0 1 17 17" fill="none" stroke="#3276b5" stroke-width="3" stroke-linecap="round"/>
      </svg>
      <div class="phone-number">847 302 7469</div>
    </footer>
  </div>
</body>
</html>
```